Redesign of LumoWordfind.com in Bootstrap 4

Current design of LumoWordfind.com is not responsive. We need to change it to latest version of Bootstrap 4 keeping essential elements in place.

Apart from home page, we need designs for http://www.lumowordfind.com/meaning/cat also.

Coding

Number of Pages Required

2 page

Colors
34a7d8

Requirements
Must have
• Bootstrap 4

```html
<!DOCTYPE html>
<html lang="en">
<head>
<meta charset="utf-8">
<title>LumoWordfind.com</title>
<link rel="stylesheet" href="https://fonts.googleapis.com/css2?family=Open+Sans:wght@400;600;700&display=swap">
<style>
:root{
  --brand:#34a7d8;
  --orange:#f7941d;
  --ink:#2b2b2b;
  --text:#555;
  --muted:#8a8a8a;
  --sand:#f3f1ec;
  --line:#e4e4e4;
  --footer:#1d1d1f;
  --footer-bottom:#121213;
  --white:#fff;
}
*{box-sizing:border-box;margin:0;padding:0}
html,body{width:1200px;height:2956px;overflow:hidden}
body{font-family:"Open Sans",Arial,sans-serif;color:var(--text);background:var(--white);position:relative}
section,header,footer{position:absolute;left:0;width:1200px}
.abs{position:absolute}
a{color:inherit;text-decoration:none}

/* header */
.site-header{top:0;height:95px;background:var(--white);border-bottom:3px solid var(--brand)}
.brand-name{left:98px;top:30px;font-size:26px;font-weight:700;color:var(--orange);letter-spacing:-.5px}
.main-nav{left:0;top:0;height:95px;width:1200px}
.main-nav a{position:absolute;top:38px;font-size:15px;color:var(--ink)}
.main-nav a.active{color:var(--orange);border-bottom:2px solid var(--orange);padding-bottom:2px}
.btn-login{position:absolute;left:1010px;top:33px;width:90px;height:36px;background:var(--orange);color:var(--white);font-size:15px;line-height:36px;text-align:center;border-radius:3px}

/* hero */
.hero{top:95px;height:551px;overflow:hidden}
.hero-photo{left:0;top:0;width:1200px;height:551px;background:linear-gradient(100deg,#7e7a74 0%,#a49d93 30%,#8d8f92 55%,#6f7276 100%)}
.hero-title{left:560px;top:100px;font-size:42px;font-weight:600;color:var(--white)}
.hero-text{left:560px;top:172px;width:534px;font-size:26px;line-height:38px;color:var(--white);text-align:justify;font-weight:600}
.hero-arrow{top:250px;width:20px;height:34px}

/* search */
.search-band{top:646px;height:272px;background:var(--brand);text-align:center;color:var(--white)}
.search-band h1{position:absolute;top:50px;width:100%;font-size:27px;font-weight:600}
.search-band p{position:absolute;top:94px;width:100%;font-size:21px}
.search-input{left:311px;top:164px;width:377px;height:51px;background:rgba(255,255,255,.28);color:rgba(255,255,255,.75);font-size:16px;line-height:51px;padding-left:20px;text-align:left}
.search-btn{left:688px;top:164px;width:198px;height:51px;background:var(--orange);font-size:17px;line-height:51px;font-weight:600}

/* generic blocks */
.block-title{font-size:26px;font-weight:600;color:var(--ink)}
.block-sub{font-size:15px;color:var(--ink)}
.body-small{font-size:12.5px;line-height:24px;color:var(--muted);text-align:justify}
.btn-orange{background:var(--orange);color:var(--white);font-size:16px;font-weight:600;text-align:center;border-radius:2px}

/* features */
.features{top:918px;height:331px}
.feature-list{left:98px;top:102px;list-style:none}
.feature-list li{position:relative;height:39.5px;padding-left:36px;font-size:14px;color:#666}
.feature-list svg{position:absolute;left:0;top:3px}
.feature-list .free{color:var(--orange)}
.map-art{left:626px;top:24px;width:438px;height:279px;background:linear-gradient(135deg,#5cc6c4 0%,#36a6b4 60%,#3f9fb0 100%)}

/* crossword */
.crossword{top:1249px;height:331px;background:var(--sand)}
.crossword-art{left:98px;top:28px;width:492px;height:279px;background:linear-gradient(135deg,#efe9dd,#e2d9c7)}

/* addon */
.addon{top:1580px;height:335px}
.addon-tag{left:615px;top:132px;display:flex;align-items:center;gap:14px;font-size:26px;font-weight:600;color:var(--ink)}
.addon-tag i{display:block;width:22px;height:22px;background:var(--brand)}
.addon-heading{left:855px;top:114px;font-size:55px;font-weight:700;color:var(--ink);letter-spacing:-1px}
.addon-links{left:857px;top:186px;font-size:12px;color:var(--ink)}

/* phone */
.phone{top:1915px;height:331px;background:var(--sand)}
.phone-art{left:98px;top:12px;width:552px;height:309px;background:linear-gradient(160deg,#e9e8e4,#cfd3d6 60%,#e9e8e4)}
.phone-lead{font-size:15px;line-height:26px;color:#555;text-align:justify}

/* tidbit */
.tidbit{top:2246px;height:276px}
.tidbit h2{position:absolute;top:36px;width:100%;text-align:center;font-size:26px;font-weight:600;color:var(--ink)}
.tidbit-card{top:94px;width:242px;height:130px;border:1px solid var(--line);padding:16px 14px 16px 16px}
.tidbit-card h3{font-size:17px;font-weight:600;color:var(--ink);margin-bottom:12px}
.tidbit-card p{font-size:11.5px;line-height:20px;color:#666}

/* browse */
.browse{top:2522px;height:96px}
.browse-row{left:98px;top:5px;width:1004px;border-top:1px solid var(--line)}
.browse-label{left:98px;top:19px;font-size:16px;color:var(--brand);font-weight:600}
.browse-letters{left:270px;top:19px;font-size:16px;color:#c4c4c4;display:flex}
.browse-letters span{width:32.6px;text-align:center}
.browse-letters .on{color:var(--brand);border-bottom:2px solid var(--brand);padding-bottom:4px}

/* footer */
.site-footer{top:2618px;height:268px;background:var(--footer);color:var(--white)}
.footer-col{top:34px}
.footer-col h4{font-size:22px;font-weight:600;margin-bottom:14px}
.footer-col ul{list-style:none}
.footer-col li{font-size:14px;color:#bdbdbd;height:39.3px;padding-left:26px;position:relative}
.footer-col li::before{content:"";position:absolute;left:2px;top:8px;width:6px;height:6px;border-radius:50%;background:var(--brand)}
.footer-bottom{top:2886px;height:70px;background:var(--footer-bottom);color:#8c8c8c;font-size:12px}
.footer-brand{left:98px;top:22px;font-size:20px;font-weight:700;color:#555}
.copyright{left:0;width:1200px;top:27px;text-align:center}
.footer-code{left:1136px;top:27px}
</style>
</head>
<body>

<header class="site-header">
  <div class="abs brand-name">Lumo Wordfind</div>
  <nav class="abs main-nav">
    <a class="active" style="left:390px">Home</a>
    <a style="left:478px">Idioms</a>
    <a style="left:572px">Common Errors</a>
    <a style="left:723px">Crossword</a>
    <a style="left:842px">Blog</a>
    <a style="left:918px">Contact</a>
    <a class="btn-login">Log In</a>
  </nav>
</header>

<section class="hero">
  <div class="abs hero-photo" role="img" aria-label="Photo of a stack of books with an open laptop leaning on them"></div>
  <div class="abs hero-title">LumoWordfind.com</div>
  <p class="abs hero-text">The standard chunk of Lorem Ipsum used since the 1500s is reproduced below for those interested</p>
  <svg class="abs hero-arrow" style="left:30px" viewBox="0 0 20 34"><path d="M17 2 3 17l14 15" fill="none" stroke="#fff" stroke-opacity=".7" stroke-width="2"/></svg>
  <svg class="abs hero-arrow" style="left:1150px" viewBox="0 0 20 34"><path d="M3 2l14 15L3 32" fill="none" stroke="#fff" stroke-opacity=".7" stroke-width="2"/></svg>
</section>

<section class="search-band">
  <h1>Welcome To Lumo Wordfind</h1>
  <p>Lumo English Dictionary Search For The Word You Want</p>
  <div class="abs search-input">Enter The Word</div>
  <div class="abs search-btn">Search Now</div>
</section>

<section class="features">
  <h2 class="abs block-title" style="left:98px;top:44px">Search, Save and Master Words</h2>
  <ul class="abs feature-list">
    <li><svg width="14" height="12" viewBox="0 0 14 12"><path d="M1 6l4 4 8-9" fill="none" stroke="#34a7d8" stroke-width="2"/></svg>Search from more than 300,000 words and phrases</li>
    <li><svg width="14" height="12" viewBox="0 0 14 12"><path d="M1 6l4 4 8-9" fill="none" stroke="#34a7d8" stroke-width="2"/></svg>Multiple usages to clarify the context</li>
    <li><svg width="14" height="12" viewBox="0 0 14 12"><path d="M1 6l4 4 8-9" fill="none" stroke="#34a7d8" stroke-width="2"/></svg>Audio, phonetics, meanings, synonyms and antonyms</li>
    <li><svg width="14" height="12" viewBox="0 0 14 12"><path d="M1 6l4 4 8-9" fill="none" stroke="#34a7d8" stroke-width="2"/></svg>Save the words to your personal deck and access from anywhere</li>
    <li><svg width="14" height="12" viewBox="0 0 14 12"><path d="M1 6l4 4 8-9" fill="none" stroke="#34a7d8" stroke-width="2"/></svg>It's <span class="free">FREE</span></li>
  </ul>
  <div class="abs map-art" role="img" aria-label="Illustrated world map with cartoon people saying hello in many languages"></div>
</section>

<section class="crossword">
  <div class="abs crossword-art" role="img" aria-label="Illustration of a crossword grid with cartoon characters around it"></div>
  <h2 class="abs block-title" style="left:672px;top:44px">Daily Crossword</h2>
  <p class="abs block-sub" style="left:672px;top:90px">Crossword Lovers! <span style="font-size:11px;color:#777">Take this daily crossword challenge from Lumo Wordfind.</span></p>
  <p class="abs body-small" style="left:672px;top:124px;width:432px">There are many variations of passages of Lorem Ipsum available, but the majority have suffered alteration in some form, by injected humour, or randomised words which don't look even slightly believable. If you are going to use a passage of Lorem Ipsum, you need to be sure</p>
  <div class="abs btn-orange" style="left:674px;top:238px;width:140px;height:44px;line-height:44px">Solve Now</div>
</section>

<section class="addon">
  <h2 class="abs block-title" style="left:98px;top:44px">Quillway Addon</h2>
  <p class="abs block-sub" style="left:98px;top:90px">Quick Dictionary Lookup from LumoWordfind.com</p>
  <p class="abs body-small" style="left:98px;top:124px;width:460px;color:#777">Add this tool to your Quillway and quickly look up for definitions from any website without leaving the page. Provides quick look up of difficult words with audio, phonetics and usages. Just press (Shift + Mouse Right Click) on any word and all the information pops up in the same window.</p>
  <div class="abs btn-orange" style="left:98px;top:238px;width:345px;height:44px;line-height:44px">Only with Quillway — Get Quillway Now!</div>
  <div class="abs addon-tag"><i></i>Quillway</div>
  <div class="abs addon-heading">ADD-ONS</div>
  <div class="abs addon-links">Extensions &nbsp; | &nbsp; Themes &nbsp; | &nbsp; Collections &nbsp;&gt;&gt;</div>
</section>

<section class="phone">
  <div class="abs phone-art" role="img" aria-label="Two smartphones showing the Lumo Wordfind app"></div>
  <h2 class="abs block-title" style="left:674px;top:44px">Designed for Pebblephone</h2>
  <p class="abs phone-lead" style="left:674px;top:84px;width:430px">Lumo Wordfind is specially designed for your Pebblephone to quickly lookup meaning, usages and audio of words.</p>
  <p class="abs body-small" style="left:674px;top:152px;width:430px">There are many variations of passages of Lorem Ipsum available, but the majority have suffered alteration in some form, by injected humour, or randomised words which don't look even slightly believable.</p>
  <p class="abs body-small" style="left:674px;top:240px;width:430px">If you are going to use a passage of Lorem Ipsum, you need to be sure alteration in some form, by injected humour, or randomised words which don't look even slightly believable.</p>
</section>

<section class="tidbit">
  <h2>English Tidbit</h2>
  <article class="abs tidbit-card" style="left:98px"><h3>gaffe/gaff</h3><p>"Gaffe" is a social blunder and "gaff" is a large hook. Be warned not to make the gaffe of mixing it up with gaff.</p></article>
  <article class="abs tidbit-card" style="left:351px"><h3>gaffe/gaff</h3><p>"Gaffe" is a social blunder and "gaff" is a large hook. Be warned not to make the gaffe of mixing it up with gaff.</p></article>
  <article class="abs tidbit-card" style="left:605px"><h3>gaffe/gaff</h3><p>"Gaffe" is a social blunder and "gaff" is a large hook. Be warned not to make the gaffe of mixing it up with gaff.</p></article>
  <article class="abs tidbit-card" style="left:859px"><h3>gaffe/gaff</h3><p>"Gaffe" is a social blunder and "gaff" is a large hook. Be warned not to make the gaffe of mixing it up with gaff.</p></article>
</section>

<section class="browse">
  <div class="abs browse-row"></div>
  <div class="abs browse-label">Browse Dictionary</div>
  <div class="abs browse-letters">
    <span class="on">A</span><span>B</span><span>C</span><span>D</span><span>E</span><span>F</span><span>G</span><span>H</span><span>I</span><span>J</span><span>K</span><span>L</span><span>M</span><span>N</span><span>O</span><span>P</span><span>Q</span><span>R</span><span>S</span><span>T</span><span>U</span><span>V</span><span>W</span><span>X</span><span>Y</span><span>Z</span>
  </div>
</section>

<footer class="site-footer">
  <div class="abs footer-col" style="left:98px"><h4>LumoWordfind.com</h4><ul><li>FAQ</li><li>Contact</li><li>Blog</li></ul></div>
  <div class="abs footer-col" style="left:416px"><h4>Legal</h4><ul><li>Privacy policy</li><li>Terms of use</li></ul></div>
  <div class="abs footer-col" style="left:654px"><h4>Others</h4><ul><li>Popular words</li><li>Common errors in english</li><li>GEO online</li></ul></div>
  <div class="abs footer-col" style="left:952px"><h4>Lumo wordfind</h4><ul><li>Meaning/Definition</li><li>Audio</li><li>Phonetics</li><li>More</li></ul></div>
</footer>
<footer class="footer-bottom">
  <div class="abs footer-brand">Lumo Wordfind</div>
  <div class="abs copyright">Copyrights@2016 Lumo Wordfind . all rights reserved</div>
  <div class="abs footer-code">C15</div>
</footer>

</body>
</html>
```